Aquavelo- plumbing service flyer

Hello,
We would like to create flyer for our plumbing company Aquavelo
- we have 2 web domains
aquavelo-example.hr ( official)
preuredjenjedoma-example.hr ( for bathroom renovation)

- we would like to create a similar Z-fold flyer ( from A4 paper) for our services
- We are sending images used on our websites. Of Course, it is allowed to put some of their own. Depending on design
- sending word with text which should go on each page. Text can be modified but in the sense of a page. The massage on a page should be as in word.
What is important to us:
- to stay in blue color
- It should be 1 page when fully open. So it looks like the complete page of information
- first/front page should be with our logo and phone number. more focus on emergency plumbing.
- back page should be about bathroom remodeling. Not necessary but would be received more points
- please don't use images of regular plumbers from Pixelvault and similar. we don't want to use this stock's regular images as all others.

Target Market(s)

Bathroom remodeling and emergency plumbing

Industry/Entity Type

Construction-Plumbing

Colors
0054AA
0677BA
7BADD7
CADEEF
E8F1F8

Requirements
Must have
• Logo

```html
<!DOCTYPE html>
<html lang="hr">
<head>
<meta charset="utf-8">
<title>Aquavelo – Z-fold letak</title>
<link href="https://fonts.googleapis.com/css2?family=Anton&family=Poppins:ital,wght@0,400;0,500;0,600;0,700;1,500&display=swap" rel="stylesheet">
<style>
:root{
  --navy:#0c1d48;
  --navy-deep:#0f1652;
  --blue:#0054AA;
  --blue-mid:#0677BA;
  --sky:#4fc3ee;
  --sky-soft:#7BADD7;
  --pale:#CADEEF;
  --ice:#E8F1F8;
  --yellow:#f7b21b;
  --red:#e61b1b;
  --purple:#6a2ee0;
  --hex-fill:#e8e6fb;
  --hex-line:#7d6ee8;
  --white:#ffffff;
}
*{margin:0;padding:0;box-sizing:border-box}
html,body{width:785px;height:1200px;overflow:hidden;background:#fff}
body{position:relative;font-family:"Poppins",sans-serif;color:var(--white)}
.sheet{position:absolute;left:50px;width:690px;height:487px;overflow:hidden;box-shadow:0 2px 8px rgba(0,0,0,.25)}
.sheet-outside{top:101px;background:var(--navy)}
.sheet-inside{top:650px;background:var(--navy-deep)}
.abs{position:absolute}
.ctr{position:absolute;transform:translateX(-50%);text-align:center;white-space:nowrap}
.display{font-family:"Anton",sans-serif;font-weight:400;text-transform:uppercase;line-height:1}
svg.bg{position:absolute;left:0;top:0}

/* outside – left panel */
.reno-title{left:21px;top:20px;font-size:15px;line-height:1.05}
.reno-copy{left:21px;top:62px;width:170px;font-size:6.3px;line-height:1.25}
.reno-copy p{margin-bottom:7px}
.steps-title{left:21px;top:222px;font-size:16px;line-height:1.05}
.step{position:absolute;left:21px;display:flex;align-items:flex-start;gap:12px;font-size:9.3px;font-weight:500;line-height:1.6}
.step-num{width:20px;height:20px;flex:none;clip-path:polygon(50% 0,100% 25%,100% 75%,50% 100%,0 75%,0 25%);background:var(--white);display:flex;align-items:center;justify-content:center}
.step-num span{width:16px;height:16px;clip-path:polygon(50% 0,100% 25%,100% 75%,50% 100%,0 75%,0 25%);background:var(--navy);display:flex;align-items:center;justify-content:center;font-family:"Anton",sans-serif;font-size:8px}

/* outside – middle panel */
.brand-mark{left:298px;top:14px;width:94px;height:94px;border-radius:50%;background:radial-gradient(circle at 50% 40%,var(--sky),var(--blue) 70%);border:3px solid var(--white)}
.brand-name{left:345px;top:80px;font-size:22px;color:var(--white)}
.clock{left:321px;top:131px;width:48px;height:48px;border-radius:50%;background:var(--red);border:2px solid var(--white);display:flex;align-items:center;justify-content:center;font-family:"Anton",sans-serif;font-size:16px;z-index:2}
.emergency-box{left:262px;top:172px;width:166px;height:57px;background:var(--red);border:1.5px solid var(--white);border-radius:5px}
.emergency-label{left:345px;top:184px;font-size:12px;letter-spacing:1.5px;color:var(--yellow)}
.emergency-phone{left:345px;top:200px;font-size:24px;color:var(--white)}
.contact-icon{position:absolute;width:26px;height:26px;border-radius:50%;background:var(--yellow);display:flex;align-items:center;justify-content:center;transform:translateX(-50%)}
.contact-line{font-size:10.5px;line-height:1.25}
.mobile{left:345px;top:266px;font-size:21px;color:var(--yellow)}
.social{position:absolute;top:447px;width:19px;height:19px;border-radius:50%;background:var(--white);transform:translateX(-50%)}

/* outside – right panel */
.slogan{left:494px;top:20px;width:180px;text-align:right;font-size:33px;line-height:1}
.slogan .accent{color:var(--sky)}
.hero-art{left:490px;top:130px;width:156px;height:150px;border-radius:50%;background:radial-gradient(circle,var(--blue-mid) 0%,var(--blue) 50%,rgba(12,29,72,0) 72%)}
.services-title{left:576px;top:284px;font-size:13.5px;font-weight:700;letter-spacing:.3px}
.hex{position:absolute;clip-path:polygon(50% 0,100% 25%,100% 75%,50% 100%,0 75%,0 25%);background:var(--white);transform:translate(-50%,-50%);display:flex;align-items:center;justify-content:center}
.hex::after{content:"";width:88%;height:88%;clip-path:polygon(50% 0,100% 25%,100% 75%,50% 100%,0 75%,0 25%);background:var(--hex-fill)}
.hex-sm{width:38px;height:42px}
.hex-md{width:46px;height:50px}
.svc-label{font-family:"Anton",sans-serif;font-size:8px;line-height:1.2}
.open-note{left:576px;top:380px;font-size:9.3px;line-height:1.2}
.open-note b{color:var(--sky);font-weight:400}
.mini-badge{left:541px;top:421px;width:100px;height:28px;background:var(--red);border-radius:3px}
.mini-clock{left:508px;top:418px;width:34px;height:34px;border-radius:50%;background:var(--red);border:2px solid var(--white);display:flex;align-items:center;justify-content:center;font-family:"Anton",sans-serif;font-size:12px}
.mini-label{left:592px;top:424px;font-size:6.5px;letter-spacing:.8px;color:var(--white)}
.mini-phone{left:592px;top:433px;font-size:12px;color:var(--yellow)}
.right-web{left:576px;top:453px;font-size:11px}

/* inside */
.service-disc{position:absolute;width:146px;height:146px;border-radius:50%;border:4px solid var(--yellow);overflow:hidden;transform:translateX(-50%)}
.disc-art{position:absolute;left:0;top:0;width:100%;height:62%}
.disc-band{position:absolute;left:0;bottom:0;width:100%;height:42%;border-radius:50% 50% 0 0/20% 20% 0 0}
.disc-title{position:absolute;left:0;width:100%;text-align:center;top:91px;font-size:24px;color:var(--white)}
.disc-sub{position:absolute;left:0;width:100%;text-align:center;top:118px;font-size:13px;font-style:italic;font-weight:500}
.disc-plumbing .disc-art{background:linear-gradient(#1788d6,#0d3f8a)}
.disc-plumbing .disc-band{background:#0aa6e8}
.disc-drain .disc-art{background:linear-gradient(#e8552c,#a92a12)}
.disc-drain .disc-band{background:#f4683d}
.disc-leak .disc-art{background:linear-gradient(#2f8f6a,#1e5d52)}
.disc-leak .disc-band{background:#62ab4e}
.col-title{font-size:12.5px;font-weight:700;line-height:1.2}
.col-copy{font-size:7.3px;line-height:1.22;white-space:normal}
.icon-label{font-size:8px;font-weight:600;line-height:1.2}
.inside-web{left:395px;top:1111px;font-size:11px;font-weight:500;letter-spacing:2px;color:var(--navy-deep)}
</style>
</head>
<body>

<!-- OUTSIDE SHEET -->
<section class="sheet sheet-outside" aria-label="Vanjska strana letka">
  <svg class="bg" width="690" height="487" viewBox="0 0 690 487">
    <defs>
      <linearGradient id="renoPhoto" x1="0" y1="0" x2="1" y2="1">
        <stop offset="0" stop-color="#3fa3d8"/><stop offset="1" stop-color="#2a88c4"/>
      </linearGradient>
      <linearGradient id="renoPhotoDark" x1="0" y1="0" x2="0" y2="1">
        <stop offset="0" stop-color="#12467a"/><stop offset="1" stop-color="#0c2454"/>
      </linearGradient>
    </defs>
    <g role="img" aria-label="Fotografija majstora pri radu u kupaonici">
      <path d="M0,0 H196 Q252,230 192,487 H0 Z" fill="url(#renoPhotoDark)"/>
      <path d="M0,0 H196 Q236,110 224,245 Q120,180 0,208 Z" fill="url(#renoPhoto)"/>
    </g>
    <path d="M0,208 Q110,178 224,245" fill="none" stroke="#2fc07a" stroke-width="3"/>
    <path d="M196,0 Q252,230 192,487" fill="none" stroke="var(--yellow)" stroke-width="3"/>
    <path d="M494,6 Q440,200 499,400" fill="none" stroke="var(--yellow)" stroke-width="3"/>
  </svg>

  <h2 class="abs display reno-title">Adaptacija<br>kupaonice</h2>
  <div class="abs reno-copy">
    <p>Za vas, kupaonica je mjesto gdje započinjete i završavate svoj dan. Tu nalazite mir, čistoću i relaksaciju.</p>
    <p>Za nas, kupaonica i instalacije su začepljeni odvodi, stare pločice i puknuti odvodi koje treba popraviti.</p>
    <p>Dobar savjet zlata vrijedi. Naši stručnjaci će vam pružiti kompletnu uslugu adaptacije i renovacije kupaonice, od planiranja do realizacije.</p>
    <p>Dopustite nam da Vam pomognemo u stvaranju Vaše nove kupaonice.</p>
    <p>Nazovite nas s povjerenjem.</p>
  </div>

  <h2 class="abs display steps-title">Koraci adaptacije<br>kupaonice :</h2>
  <div class="step" style="top:266px"><div class="step-num"><span>01</span></div>Planiranje</div>
  <div class="step" style="top:293px"><div class="step-num"><span>02</span></div>Rušenje i skidanje pločica</div>
  <div class="step" style="top:321px"><div class="step-num"><span>03</span></div>Postavljanje instalacija</div>
  <div class="step" style="top:349px"><div class="step-num"><span>04</span></div>Postavljanje struje</div>
  <div class="step" style="top:377px"><div class="step-num"><span>05</span></div>Keramičarski radovi</div>
  <div class="step" style="top:405px"><div class="step-num"><span>06</span></div>Montaža kupaonske<br>sanitarije</div>
  <div class="step" style="top:448px"><div class="step-num"><span>07</span></div>Završno čišćenje</div>

  <div class="abs brand-mark" role="img" aria-label="Ilustracija maskote vodoinstalatera"></div>
  <div class="ctr display brand-name">Aquavelo</div>

  <div class="abs clock">24</div>
  <div class="abs emergency-box"></div>
  <div class="ctr display emergency-label">Emergency plumbing</div>
  <div class="ctr display emergency-phone">095-000-1234</div>

  <div class="contact-icon" style="left:345px;top:238px">
    <svg width="13" height="13" viewBox="0 0 24 24"><path d="M6.6 10.8a15 15 0 006.6 6.6l2.2-2.2a1 1 0 011-.25 11.4 11.4 0 003.6.57 1 1 0 011 1V20a1 1 0 01-1 1A17 17 0 013 4a1 1 0 011-1h3.5a1 1 0 011 1c0 1.25.2 2.45.57 3.57a1 1 0 01-.25 1z" fill="var(--navy)"/></svg>
  </div>
  <div class="ctr display mobile">+385 91 000 4567</div>

  <div class="contact-icon" style="left:345px;top:294px">
    <svg width="13" height="13" viewBox="0 0 24 24"><rect x="3" y="6" width="18" height="13" rx="1" fill="none" stroke="var(--navy)" stroke-width="2"/><path d="M3 7l9 7 9-7" fill="none" stroke="var(--navy)" stroke-width="2"/></svg>
  </div>
  <div class="ctr contact-line" style="left:345px;top:321px">info@aquavelo-example.hr</div>

  <div class="contact-icon" style="left:345px;top:338px">
    <svg width="13" height="13" viewBox="0 0 24 24"><path d="M12 2a7 7 0 00-7 7c0 5 7 13 7 13s7-8 7-13a7 7 0 00-7-7zm0 9.5A2.5 2.5 0 1112 6.5a2.5 2.5 0 010 5z" fill="var(--navy)"/></svg>
  </div>
  <div class="ctr contact-line" style="left:345px;top:366px">Dostupni smo 24/7 jer hitne<br>intervencije ne mogu čekati.</div>

  <div class="contact-icon" style="left:345px;top:397px">
    <svg width="13" height="13" viewBox="0 0 24 24"><circle cx="12" cy="12" r="9" fill="none" stroke="var(--navy)" stroke-width="2"/><path d="M3 12h18M12 3c3 3 3 15 0 18M12 3c-3 3-3 15 0 18" fill="none" stroke="var(--navy)" stroke-width="1.5"/></svg>
  </div>
  <div class="ctr contact-line" style="left:345px;top:425px">www.aquavelo-example.com</div>

  <div class="social" style="left:307px" aria-hidden="true"></div>
  <div class="social" style="left:332px" aria-hidden="true"></div>
  <div class="social" style="left:358px" aria-hidden="true"></div>
  <div class="social" style="left:383px" aria-hidden="true"></div>

  <h1 class="abs display slogan">Let the water<br><span class="accent">stay in the</span><br>pipes only</h1>
  <div class="abs hero-art" role="img" aria-label="Ilustracija maskote vodoinstalatera s cijevi na ramenu"></div>
  <div class="ctr services-title">AQUAVELO USLUGE:</div>
  <div class="hex hex-sm" style="left:516px;top:325px"></div>
  <div class="hex hex-sm" style="left:571px;top:325px"></div>
  <div class="hex hex-sm" style="left:626px;top:325px"></div>
  <div class="ctr svc-label" style="left:516px;top:350px">Hitne<br>intervencije</div>
  <div class="ctr svc-label" style="left:571px;top:350px">Adapatacija<br>kupaonica</div>
  <div class="ctr svc-label" style="left:626px;top:350px">Detekcija<br>curenja</div>
  <div class="ctr open-note">We’re open <b>24/7/365</b> because<br>plumbing emergencies<br>don’t wait ...</div>
  <div class="abs mini-badge"></div>
  <div class="abs mini-clock">24</div>
  <div class="ctr display mini-label">Emergency plumbing</div>
  <div class="ctr display mini-phone">095-000-1234</div>
  <div class="ctr right-web">aquavelo-example.hr</div>
</section>

<!-- INSIDE SHEET -->
<section class="sheet sheet-inside" aria-label="Unutarnja strana letka">
  <svg class="bg" width="690" height="487" viewBox="0 0 690 487">
    <defs>
      <linearGradient id="splash" x1="0" y1="0" x2="0" y2="1">
        <stop offset="0" stop-color="#7fd3f4"/><stop offset="1" stop-color="#4cbdea"/>
      </linearGradient>
    </defs>
    <rect x="231" y="100" width="226" height="370" fill="var(--purple)"/>
    <path d="M0,0 H690 Q345,235 0,0 Z" fill="url(#splash)" role="img" aria-label="Prskanje vode u pozadini"/>
    <path d="M0,487 Q345,400 690,487" fill="#1d2a6e"/>
    <path d="M60,487 Q345,420 630,487 Z" fill="#59c6ee"/>
  </svg>

  <div class="service-disc disc-plumbing" style="left:110px;top:30px">
    <div class="disc-art" role="img" aria-label="Maskota vodoinstalatera"></div>
    <div class="disc-band"></div>
    <div class="disc-title display">Plumbing</div>
    <div class="disc-sub">Services</div>
  </div>
  <div class="service-disc disc-drain" style="left:348px;top:30px">
    <div class="disc-art" role="img" aria-label="Maskota vodoinstalatera"></div>
    <div class="disc-band"></div>
    <div class="disc-title display">Drain</div>
    <div class="disc-sub">Cleaning</div>
  </div>
  <div class="service-disc disc-leak" style="left:571px;top:30px">
    <div class="disc-art" role="img" aria-label="Maskota vodoinstalatera"></div>
    <div class="disc-band"></div>
    <div class="disc-title display">Leak</div>
    <div class="disc-sub">Detection</div>
  </div>

  <div class="ctr col-title" style="left:112px;top:188px">ADAPTACIJA<br>KUPAONICA</div>
  <div class="ctr col-copy" style="left:112px;top:226px;width:160px">Naši stručnjaci će vam pružiti kompletnu uslugu adaptacije i renovacije kupaonice. Dopustite nam da Vam pomognemo u stvaranju Vaše nove kupaonice.</div>

  <div class="ctr col-title" style="left:345px;top:190px">HITNE<br>INTERVENCIJE</div>
  <div class="ctr col-copy" style="left:345px;top:226px;width:180px">Hitno vam treba odčepljivanje odvoda, sanacija ili dijagnostika puknuća cijevi? Kontaktirajte nas odmah i spriječite veću štetu!</div>

  <div class="ctr col-title" style="left:579px;top:190px">DETEKCIJA<br>CURENJA</div>
  <div class="ctr col-copy" style="left:579px;top:226px;width:180px">Pronalaženje curenja cijevi nekad može biti mukotrpan posao. Nekad izvor može doći iz neočekivanih izvora. Zato naš tim je opremljen profesionalnim alatima za svaki problem.</div>

  <!-- plumbing column -->
  <div class="hex hex-md" style="left:47px;top:302px"></div>
  <div class="hex hex-md" style="left:113px;top:302px"></div>
  <div class="hex hex-md" style="left:182px;top:302px"></div>
  <div class="ctr icon-label" style="left:47px;top:329px">Burst Pipes</div>
  <div class="ctr icon-label" style="left:113px;top:329px">Toilet Repair<br>&amp; Installation</div>
  <div class="ctr icon-label" style="left:182px;top:329px">Plumbing<br>Repairs</div>
  <div class="hex hex-md" style="left:47px;top:379px"></div>
  <div class="hex hex-md" style="left:113px;top:379px"></div>
  <div class="hex hex-md" style="left:182px;top:379px"></div>
  <div class="ctr icon-label" style="left:47px;top:406px">Water<br>Heaters</div>
  <div class="ctr icon-label" style="left:113px;top:410px">Shower<br>Repair<br>&amp; Installation</div>
  <div class="ctr icon-label" style="left:182px;top:410px">Air<br>conditioning</div>

  <!-- drain column -->
  <div class="hex hex-md" style="left:297px;top:303px"></div>
  <div class="hex hex-md" style="left:388px;top:303px"></div>
  <div class="ctr icon-label" style="left:297px;top:332px">Pipelining</div>
  <div class="ctr icon-label" style="left:388px;top:330px">Rooter<br>Services</div>
  <div class="hex hex-md" style="left:297px;top:386px"></div>
  <div class="hex hex-md" style="left:388px;top:386px"></div>
  <div class="ctr icon-label" style="left:297px;top:414px">Drain Cleaning</div>
  <div class="ctr icon-label" style="left:388px;top:414px">Drain Repair</div>

  <!-- leak column -->
  <div class="hex hex-md" style="left:504px;top:303px"></div>
  <div class="hex hex-md" style="left:572px;top:303px"></div>
  <div class="hex hex-md" style="left:640px;top:303px"></div>
  <div class="ctr icon-label" style="left:504px;top:330px">Leak<br>Detection</div>
  <div class="ctr icon-label" style="left:572px;top:330px">Gas Lines</div>
  <div class="ctr icon-label" style="left:640px;top:331px">Garbage<br>Disposals</div>
  <div class="hex hex-md" style="left:525px;top:386px"></div>
  <div class="hex hex-md" style="left:614px;top:386px"></div>
  <div class="ctr icon-label" style="left:525px;top:415px">Pipe Repair</div>
  <div class="ctr icon-label" style="left:614px;top:415px">Gas Valves</div>
</section>

<div class="ctr inside-web">www.aquavelo-example.hr</div>

</body>
</html>
```